Website Development for vaultmerrow.com.au

Build a new Wordpress/Responsive website for vaultmerrow.com.au

Target Market(s)

Compliance Managers, Risk Managers, Information Security and Cyber Security Professionals, Chief Data/Digital Officers, Chief Operating/Financial Officers, Business Continuity Professionals, Disaster Recovery Planners, Small Business Owners, Local/Federal Government entities

Industry/Entity Type

Data Service

Coding

Coded - Design and coding required

Number of Pages Required

5+ page

Font styles to use
Sans Serif

Colors

Designer to choose colors to be used in the design.

Requirements
Must have
• 1. Site Structure: Home Page plus the following chapter-pages for a) Services b) About c) Resources d) Blog e) Contact Us
• 2. Prefer site to built on wordpress and we can purchase a theme if needed (we currently use Kelp9 for other sites)
• 3. Blog needs to be wordpress based
• 4. We will host the site ourselves on our own servers
• 5. Responsive Design
Nice to have
• 1. Livechat capability/interface
• 2. Capability for marketing automation integration (such as hubspot, marketo, infusionsoft etc)
• 3. Capability for CRM integration (Salesforce)

```html
<!DOCTYPE html>
<html lang="en">
<head>
<meta charset="utf-8">
<title>Vaultmerrow – Home</title>
<link href="https://fonts.googleapis.com/css2?family=Lato:wght@300;400;700;900&display=swap" rel="stylesheet">
<style>
:root{
  --red:#e3131b;
  --red-dark:#c40d14;
  --ink:#1b1b1b;
  --text:#333;
  --muted:#777;
  --light:#f2f2f2;
  --ghost:rgba(0,0,0,.07);
  --ghost-light:rgba(255,255,255,.12);
  --dark:#161616;
  --white:#fff;
}
*{box-sizing:border-box;margin:0;padding:0}
html,body{width:1200px;height:4972px;overflow:hidden}
body{font-family:'Lato',sans-serif;color:var(--text);background:var(--white);position:relative}
section,header,footer{position:absolute;left:0;width:1200px}
.btn{position:absolute;display:flex;align-items:center;justify-content:center;gap:8px;background:var(--red);color:var(--white);font-weight:900;font-size:15px;text-transform:uppercase;border-radius:30px;letter-spacing:.5px}
.ghost-word{position:absolute;font-weight:900;font-size:118px;color:var(--ghost);white-space:nowrap;letter-spacing:1px;line-height:1}
.section-title{position:absolute;font-weight:900;font-size:44px;color:var(--ink);text-transform:uppercase;line-height:1}
.rule{position:absolute;width:52px;height:5px;background:var(--red)}

/* hero */
.hero{top:0;height:690px}
.hero-photo{position:absolute;inset:0;background:linear-gradient(135deg,#050608 0%,#0d1a24 40%,#1a3a4c 60%,#0a0c10 100%);clip-path:polygon(0 0,100% 0,100% 100%,0 58%)}
.nav{position:absolute;top:40px;left:110px;right:113px;height:50px;display:flex;align-items:center}
.brand{display:flex;align-items:center;gap:10px;color:var(--white);font-weight:900;font-size:26px;letter-spacing:1px}
.brand-dot{width:22px;height:22px;border-radius:50%;background:var(--red)}
.menu{display:flex;gap:34px;margin-left:auto;margin-right:40px;list-style:none}
.menu li{color:var(--white);font-size:16px;font-weight:400}
.menu li.active{border-bottom:2px solid var(--white);padding-bottom:4px}
.signin{position:static;width:115px;height:42px;font-size:14px}
.hero-title{position:absolute;top:212px;width:100%;text-align:center;color:var(--white);font-weight:900;font-size:68px;letter-spacing:1px}
.hero-sub{position:absolute;top:300px;width:100%;text-align:center;color:var(--white);font-size:19px}
.hero .btn{top:367px;left:520px;width:160px;height:50px}
.scroll-down{position:absolute;top:636px;left:900px;width:50px;height:50px}

/* about */
.about{top:690px;height:660px}
.about .ghost-word{top:6px;left:110px}
.about .section-title{top:132px;left:112px}
.about .rule{top:190px;left:112px}
.about-copy{position:absolute;top:228px;left:112px;width:485px;font-size:15px;line-height:34px;color:var(--text)}
.about .btn{top:440px;left:112px;width:190px;height:60px}
.about-photo{position:absolute;top:22px;left:530px;width:670px;height:630px;background:linear-gradient(160deg,#6c7a86 0%,#b9c3cb 45%,#e8ecef 70%,#3a4149 100%);clip-path:polygon(35% 0,100% 0,100% 100%,0 100%)}

/* services */
.services{top:1350px;height:815px;background:var(--red)}
.services .ghost-word{top:78px;left:105px;color:var(--ghost-light)}
.services .section-title{top:97px;left:796px;color:var(--white)}
.services .rule{top:165px;left:1033px;background:var(--white)}
.service{position:absolute;width:300px;text-align:center;color:var(--white)}
.service svg{width:66px;height:66px}
.service h3{font-size:22px;font-weight:700;margin-top:10px}
.service p{font-size:13px;line-height:22px;margin:14px auto 0;width:240px}

/* resources */
.resources{top:2165px;height:690px;background:var(--light);clip-path:polygon(0 0,100% 0,100% 84%,0 100%)}
.resources .ghost-word{top:72px;left:265px}
.resources .section-title{top:115px;left:110px}
.resources .rule{top:174px;left:110px}
.resources-copy{position:absolute;top:232px;left:112px;width:500px;font-size:15px;line-height:34px}
.resources .btn{top:455px;left:112px;width:190px;height:60px}
.shield-art{position:absolute;top:5px;left:663px;width:464px;height:598px}

/* blog */
.blog{top:2855px;height:820px}
.blog .ghost-word{top:60px;left:310px}
.blog .section-title{top:110px;width:100%;text-align:center;left:0}
.blog .rule{top:167px;left:574px}
.post{position:absolute;top:261px;width:296px;height:388px;background:var(--white);box-shadow:0 4px 18px rgba(0,0,0,.12)}
.post-img{position:absolute;top:0;left:0;width:100%;height:216px;clip-path:polygon(0 0,100% 0,100% 85%,0 100%)}
.post-date{position:absolute;top:184px;left:30px;background:var(--red);color:var(--white);font-size:12px;font-weight:700;padding:7px 12px}
.post h4{position:absolute;top:250px;left:30px;font-size:15px;font-weight:900;color:var(--ink)}
.post p{position:absolute;top:280px;left:30px;width:236px;font-size:12px;line-height:20px;color:var(--muted)}
.post .more{position:absolute;top:340px;left:30px;font-size:12px;font-weight:900;color:var(--red)}

/* contact */
.contact{top:3760px;height:870px;background:var(--light);clip-path:polygon(0 16%,100% 0,100% 100%,0 100%)}
.contact .ghost-word{top:110px;left:298px}
.contact .section-title{top:185px;width:100%;text-align:center;left:0}
.contact .rule{top:242px;left:574px}
.field{position:absolute;left:288px;width:302px;height:42px;background:var(--white);border:1px solid #ddd;font-size:13px;color:var(--muted);padding:12px 16px}
.field.message{left:613px;width:300px;height:170px}
.contact .btn{top:548px;left:500px;width:200px;height:56px}

/* footer */
.footer{top:4530px;height:442px;background:var(--dark);clip-path:polygon(0 18%,100% 0,100% 100%,0 100%);color:var(--white)}
.footer .brand{position:absolute;top:110px;left:0;width:100%;justify-content:center;font-size:34px}
.footer-nav{position:absolute;top:180px;width:100%;display:flex;justify-content:center;gap:22px;list-style:none;font-size:16px}
.footer-nav .sep{opacity:.8}
.footer-contact{position:absolute;top:238px;width:100%;display:flex;justify-content:center;gap:22px;font-size:14px;align-items:center}
.footer-contact span{display:flex;align-items:center;gap:8px}
.copyright{position:absolute;top:285px;width:100%;text-align:center;font-size:13px}
.social{position:absolute;top:343px;left:0;width:100%;display:flex;justify-content:center;gap:20px}
.social span{width:44px;height:44px;border-radius:50%;border:1px solid rgba(255,255,255,.55)}
.livechat{position:absolute;top:396px;left:938px;width:150px;height:46px;background:var(--red);display:flex;align-items:center;justify-content:center;gap:8px;font-weight:900;font-size:15px;border-radius:6px 6px 0 0}
.chat-avatar{position:absolute;top:356px;left:900px;width:56px;height:56px;border-radius:50%;background:linear-gradient(#c9b5a4,#6f5a4b);border:3px solid var(--white)}
.badge-c9{position:absolute;top:410px;left:1138px;font-size:14px;font-weight:700}
</style>
</head>
<body>

<header class="hero">
  <div class="hero-photo" role="img" aria-label="Hands typing on a laptop with a glowing security shield overlay"></div>
  <nav class="nav">
    <div class="brand"><span class="brand-dot"></span>VAULTMERROW</div>
    <ul class="menu">
      <li class="active">Home</li><li>Services</li><li>About</li><li>Resources</li><li>Blog</li><li>Contact Us</li>
    </ul>
    <span class="btn signin">
      <svg width="13" height="13" viewBox="0 0 16 16"><circle cx="8" cy="5" r="4" fill="#fff"/><path d="M0 16c0-5 16-5 16 0z" fill="#fff"/></svg>Sign In
    </span>
  </nav>
  <h1 class="hero-title">VAULTMERROW</h1>
  <p class="hero-sub">Sed ut perspiciatis unde omnis iste natusvoluptatem</p>
  <span class="btn">Read More
    <svg width="16" height="16" viewBox="0 0 16 16"><circle cx="8" cy="8" r="8" fill="#fff"/><path d="M6 4l4 4-4 4" stroke="#e3131b" stroke-width="2" fill="none"/></svg>
  </span>
  <svg class="scroll-down" viewBox="0 0 50 50"><circle cx="25" cy="25" r="22" fill="#fff" stroke="#111" stroke-width="3"/><path d="M25 13v22M16 27l9 9 9-9" stroke="#111" stroke-width="3.5" fill="none"/></svg>
</header>

<section class="about">
  <div class="ghost-word">ABOUT US</div>
  <h2 class="section-title">About Us</h2>
  <div class="rule"></div>
  <p class="about-copy">Sed ut perspiciatis unde omnis iste natus error sit voluptatem accusan-tium doloremque laudantium, totam rem aperiam, eaque ipsa quae ab illo inventore veritatis et quasi architecto beatae vitae dicta sunt explica-bo. Nemo enim ipsam voluptatem quia voluptas sit aspernatur aut odit aut fugit, sed quia consequuntur magni dolor.</p>
  <span class="btn">Read More</span>
  <div class="about-photo" role="img" aria-label="Team working at a desk with keyboards and laptops"></div>
</section>

<section class="services">
  <div class="ghost-word">WHAT WE DO</div>
  <h2 class="section-title">Our Services</h2>
  <div class="rule"></div>

  <div class="service" style="top:265px;left:88px">
    <svg viewBox="0 0 64 64" fill="none" stroke="#fff" stroke-width="2.5"><path d="M32 8l20 34H12z"/><path d="M32 24v10M32 38v2"/><circle cx="32" cy="48" r="10"/></svg>
    <h3>Risk Management</h3>
    <p>Sed ut perspiciatis unde omnis iste natus error sit voluptatem accusantium dolor-emque laudantium totam</p>
  </div>
  <div class="service" style="top:265px;left:450px">
    <svg viewBox="0 0 64 64" fill="none" stroke="#fff" stroke-width="2.5"><rect x="14" y="14" width="36" height="36" rx="4"/><path d="M22 6v8M32 6v8M42 6v8M22 50v8M32 50v8M42 50v8M6 22h8M6 32h8M6 42h8M50 22h8M50 32h8M50 42h8"/><path d="M26 32l5 5 8-10"/></svg>
    <h3>Cyber security</h3>
    <p>Sed ut perspiciatis unde omnis iste natus error sit voluptatem accusantium dolor-emque laudantium totam</p>
  </div>
  <div class="service" style="top:265px;left:812px">
    <svg viewBox="0 0 64 64" fill="none" stroke="#fff" stroke-width="2.5"><path d="M32 6l20 8v14c0 14-9 24-20 30C21 52 12 42 12 28V14z"/><rect x="24" y="28" width="16" height="12" rx="2"/><path d="M27 28v-4a5 5 0 0110 0v4"/></svg>
    <h3>Information security</h3>
    <p>Sed ut perspiciatis unde omnis iste natus error sit voluptatem accusantium dolor-emque laudantium totam</p>
  </div>
  <div class="service" style="top:508px;left:88px">
    <svg viewBox="0 0 64 64" fill="none" stroke="#fff" stroke-width="2.5"><rect x="16" y="6" width="32" height="12" rx="2"/><rect x="16" y="22" width="32" height="12" rx="2"/><path d="M32 34v10M14 50h36"/><circle cx="32" cy="50" r="5"/></svg>
    <h3>Disaster Recovery</h3>
    <p>Sed ut perspiciatis unde omnis iste natus error sit voluptatem accusantium dolor-emque laudantium totam</p>
  </div>
  <div class="service" style="top:508px;left:450px">
    <svg viewBox="0 0 64 64" fill="none" stroke="#fff" stroke-width="2.5"><circle cx="32" cy="16" r="7"/><path d="M20 34c0-8 24-8 24 0"/><circle cx="12" cy="46" r="5"/><circle cx="52" cy="46" r="5"/><circle cx="32" cy="52" r="5"/><path d="M32 34v13M28 38l-12 5M36 38l12 5"/></svg>
    <h3>Compliance Management</h3>
    <p>Sed ut perspiciatis unde omnis iste natus error sit voluptatem accusantium dolor-emque laudantium totam</p>
  </div>
  <div class="service" style="top:508px;left:812px">
    <svg viewBox="0 0 64 64" fill="none" stroke="#fff" stroke-width="2.5"><path d="M18 44a12 12 0 010-24 16 16 0 0130 4 10 10 0 010 20z"/><rect x="26" y="30" width="14" height="12" rx="2"/><path d="M29 30v-3a4 4 0 018 0v3"/></svg>
    <h3>Data security</h3>
    <p>Sed ut perspiciatis unde omnis iste natus error sit voluptatem accusantium dolor-emque laudantium totam</p>
  </div>
</section>

<section class="resources">
  <div class="ghost-word">RESOURCES</div>
  <h2 class="section-title">Resources</h2>
  <div class="rule"></div>
  <p class="resources-copy">Nemo enim ipsam voluptatem quia voluptas sit aspernatur aut odit aut fugit, sed quia consequuntur magni dolores eos qui ratione voluptatem sequi nesciuntse porro quisquam est, qui dolorem ipsum quia dolor sit amet, consectetur, adipisci velit, sed quia non numquam eius modi tem-pora incidunt ut laboreuaerat voluptatem.</p>
  <span class="btn">Read More</span>
  <svg class="shield-art" viewBox="0 0 464 598" role="img" aria-label="Shield shape filled with a photo of engineers at monitors">
    <defs><linearGradient id="shieldFill" x1="0" y1="0" x2="1" y2="1"><stop offset="0" stop-color="#2c3c4c"/><stop offset=".5" stop-color="#8fa3b5"/><stop offset="1" stop-color="#1e2a36"/></linearGradient></defs>
    <path d="M232 0l20 24c60 20 140 28 212 20v150c0 200-110 330-232 404C110 524 0 394 0 194V44c72 8 152 0 212-20z" fill="url(#shieldFill)"/>
  </svg>
</section>

<section class="blog">
  <div class="ghost-word">BLOG POSTS</div>
  <h2 class="section-title">Blog Posts</h2>
  <div class="rule"></div>

  <article class="post" style="left:113px">
    <div class="post-img" role="img" aria-label="People reviewing documents at a desk" style="background:linear-gradient(135deg,#5a5f66,#c9ccd0)"></div>
    <span class="post-date">22 JAN,2019</span>
    <h4>UM QUIA DOLMETONSECTE</h4>
    <p>Sed ut perspiciatis unde omnis iste natus error sit voluptatem doloremque</p>
    <span class="more">READ MORE</span>
  </article>
  <article class="post" style="left:454px">
    <div class="post-img" role="img" aria-label="Keyboard with a recovery key" style="background:linear-gradient(135deg,#2e3238,#9aa3ad)"></div>
    <span class="post-date">22 JAN,2019</span>
    <h4>UM QUIA DOLMETONSECTE</h4>
    <p>Sed ut perspiciatis unde omnis iste natus error sit voluptatem doloremque</p>
    <span class="more">READ MORE</span>
  </article>
  <article class="post" style="left:792px">
    <div class="post-img" role="img" aria-label="Engineer working in a server room" style="background:linear-gradient(135deg,#3c4a56,#b4c2cc)"></div>
    <span class="post-date">22 JAN,2019</span>
    <h4>UM QUIA DOLMETONSECTE</h4>
    <p>Sed ut perspiciatis unde omnis iste natus error sit voluptatem doloremque</p>
    <span class="more">READ MORE</span>
  </article>
</section>

<section class="contact">
  <div class="ghost-word">CONTACT US</div>
  <h2 class="section-title">Stay In Touch</h2>
  <div class="rule"></div>
  <div class="field" style="top:320px">Enter Name</div>
  <div class="field" style="top:384px">Email</div>
  <div class="field" style="top:446px">Phone</div>
  <div class="field message" style="top:320px">Message</div>
  <span class="btn">Submit Message</span>
</section>

<footer class="footer">
  <div class="brand"><span class="brand-dot"></span>VAULTMERROW</div>
  <ul class="footer-nav">
    <li>HOME</li><li class="sep">/</li><li>SERVICES</li><li class="sep">/</li><li>ABOUT</li><li class="sep">/</li><li>RESOURCES</li><li class="sep">/</li><li>BLOG</li><li class="sep">/</li><li>CONTACT US</li>
  </ul>
  <div class="footer-contact">
    <span><svg width="12" height="16" viewBox="0 0 12 16"><path d="M6 0a6 6 0 016 6c0 4-6 10-6 10S0 10 0 6a6 6 0 016-6z" fill="#fff"/><circle cx="6" cy="6" r="2" fill="#161616"/></svg>32, Unde omnis iste natusrror sitdup</span><span>|</span>
    <span><svg width="14" height="14" viewBox="0 0 16 16"><path d="M3 0l3 4-2 2c1 3 3 5 6 6l2-2 4 3-2 3C7 16 0 9 0 2z" fill="#fff"/></svg>Phone : 1 888 888 8888</span><span>|</span>
    <span><svg width="16" height="12" viewBox="0 0 16 12"><rect width="16" height="12" fill="#fff"/><path d="M0 0l8 7 8-7" stroke="#161616" fill="none"/></svg>Email : info@companyname.com</span>
  </div>
  <p class="copyright">Copyright ©2019 Companyname. &nbsp;|&nbsp; Terms and Conditions</p>
  <div class="social"><span></span><span></span><span></span><span></span><span></span></div>
  <div class="chat-avatar" role="img" aria-label="Support agent avatar"></div>
  <div class="livechat">
    <svg width="18" height="16" viewBox="0 0 18 16"><path d="M2 0h14a2 2 0 012 2v8a2 2 0 01-2 2H7l-5 4v-4a2 2 0 01-2-2V2a2 2 0 012-2z" fill="#fff"/></svg>LIVE CHAT
  </div>
  <span class="badge-c9">C9</span>
</footer>

</body>
</html>
```